Business Card Design

New business card design

Target Market(s)

Residential & Commercial Property Managers

Industry/Entity Type

Plumbing Services

Contact Information for Business Card

Name - Rowan Keddle, title - Director, Phone Number - 0431 286 517, email - rowan@tbk-plumbing.com.au, Company ABN - 73 215 904 386,

Font styles to use
Sans Serif

Colors
0054AA
0677BA
7BADD7
CADEEF
E8F1F8

```html
<!DOCTYPE html>
<html lang="en">
<head>
<meta charset="utf-8">
<title>TBK Plumbing Services – Business Card</title>
<link rel="stylesheet" href="https://fonts.googleapis.com/css2?family=Montserrat:wght@300;400;600;700&display=swap">
<style>
  :root {
    --backdrop: #dcdcda;
    --card-white: #ffffff;
    --navy: #1d232b;
    --accent-blue: #29a8e0;
    --text-light: #ffffff;
    --text-muted: #8a9098;
  }
  * { box-sizing: border-box; margin: 0; padding: 0; }
  html, body {
    width: 1200px; height: 801px; overflow: hidden;
    background: var(--backdrop);
    font-family: "Montserrat", sans-serif;
  }
  .sheet {
    position: relative; width: 1200px; height: 801px;
    display: flex; align-items: center; justify-content: center; gap: 40px;
  }
  .card {
    position: relative; width: 540px; height: 309px; overflow: hidden;
    box-shadow: 0 10px 24px rgba(0,0,0,0.22);
  }
  .card-front { background: var(--card-white); }
  .card-back { background: var(--navy); }
  .card-wave { position: absolute; inset: 0; width: 100%; height: 100%; }

  .brand { position: absolute; display: flex; flex-direction: column; }
  .brand-mark { display: flex; align-items: center; gap: 8px; line-height: 1; }
  .brand-name { font-weight: 300; letter-spacing: 2px; }
  .brand-dot { border-radius: 50%; background: var(--accent-blue); }
  .brand-tagline { font-weight: 300; letter-spacing: 6px; }

  .card-front .brand { left: 34px; top: 108px; }
  .card-front .brand-name { font-size: 62px; color: var(--navy); }
  .card-front .brand-dot { width: 12px; height: 12px; margin-top: 26px; }
  .card-front .brand-tagline { font-size: 9px; color: var(--text-muted); margin-top: 6px; }

  .card-back .brand { left: 0; right: 0; top: 88px; align-items: center; }
  .card-back .brand-name { font-size: 96px; color: var(--text-light); }
  .card-back .brand-dot { width: 18px; height: 18px; margin-top: 40px; }
  .card-back .brand-tagline { font-size: 12px; color: var(--text-light); letter-spacing: 10px; margin-top: 10px; }

  .contact {
    position: absolute; right: 28px; top: 96px;
    display: flex; flex-direction: column; align-items: flex-end;
    color: var(--text-light);
  }
  .contact-name { font-size: 20px; font-weight: 700; color: var(--accent-blue); }
  .contact-role { font-size: 12px; font-weight: 400; margin-top: 2px; }
  .contact-line { display: flex; align-items: center; gap: 6px; font-size: 11px; font-weight: 400; margin-top: 8px; }
  .contact-line:first-of-type { margin-top: 14px; }
  .contact-label { color: var(--accent-blue); }
  .contact-icon { width: 11px; height: 11px; fill: var(--accent-blue); }
</style>
</head>
<body>
<main class="sheet">
  <section class="card card-front">
    <svg class="card-wave" viewBox="0 0 540 309" preserveAspectRatio="none" aria-hidden="true">
      <path d="M395 0 C300 18 292 120 250 200 C210 282 140 309 80 309 L540 309 L540 0 Z" fill="#ffffff"/>
      <path d="M380 0 C290 20 278 120 236 200 C196 280 130 309 70 309 L100 309 C160 300 220 270 256 200 C298 118 306 26 396 0 Z" fill="#29a8e0"/>
      <path d="M410 0 C318 20 310 120 268 200 C230 278 170 309 110 309 L540 309 L540 0 Z" fill="#1d232b"/>
    </svg>
    <div class="brand">
      <div class="brand-mark"><span class="brand-name">tbk</span><span class="brand-dot"></span></div>
      <span class="brand-tagline">plumbing services</span>
    </div>
    <div class="contact">
      <span class="contact-name">Rowan Keddle</span>
      <span class="contact-role">Director</span>
      <span class="contact-line"><span class="contact-label">ABN</span> - 73 215 904 386</span>
      <span class="contact-line">0431 286 517
        <svg class="contact-icon" viewBox="0 0 24 24" aria-hidden="true"><path d="M6.6 10.8a15.1 15.1 0 0 0 6.6 6.6l2.2-2.2c.3-.3.7-.4 1-.2 1.1.4 2.3.6 3.6.6.6 0 1 .4 1 1V20c0 .6-.4 1-1 1A17 17 0 0 1 3 4c0-.6.4-1 1-1h3.5c.6 0 1 .4 1 1 0 1.3.2 2.5.6 3.6.1.3 0 .7-.2 1z"/></svg>
      </span>
      <span class="contact-line">rowan@tbk-plumbing.com.au
        <svg class="contact-icon" viewBox="0 0 24 24" aria-hidden="true"><path d="M2 5h20v14H2z M4 7v.4l8 5 8-5V7l-8 5z" fill-rule="evenodd"/></svg>
      </span>
    </div>
  </section>

  <section class="card card-back">
    <div class="brand">
      <div class="brand-mark"><span class="brand-name">tbk</span><span class="brand-dot"></span></div>
      <span class="brand-tagline">plumbing services</span>
    </div>
  </section>
</main>
</body>
</html>
```